Velk Partners Building Business Cards

We need a business card that reflects our business as "Solar Experts" in San Diego. Browse our website www.velkpartners.example our License needs to be displayed as "CSLB# 3867140" our phone number is (619) 555-0187

Save thousands on your electric bills and increase the value of your home while helping to protect the environment. Our solar installation experts will help you design the system that's right for you, using only the highest quality equipment that will look great and give you ideal performance. Our goal is to make you energy independent, and get your electric bill to 0.

Paul Osterby
(619) 555-0187
paul@velkpartners.example

Target Market(s)

Home owners in san diego looking for solar

Industry/Entity Type

Solar Energy

Contact Information for Business Card

Paul Osterby
(619) 555-0187
paul@velkpartners.example

Font styles to use
Other font styles liked:
• Use our logo font

Requirements
Must have
• License needs to be displayed as "CSLB# 3867140" our phone number is (619) 555-0187
Nice to have
• Real images of rooftop home solar in san diego
Should not have
• our business address

```html
<!DOCTYPE html>
<html lang="en">
<head>
<meta charset="utf-8">
<title>Velk Partners Building – Business Cards</title>
<link href="https://fonts.googleapis.com/css2?family=Open+Sans:wght@400;700&display=swap" rel="stylesheet">
<style>
  :root {
    --bg: #e9e7e4;
    --card-black: #0d0e10;
    --brand-blue: #2a4f9c;
    --brand-gold: #f4b120;
    --text-light: #e6e6e6;
    --rule-blue: #2f5ac0;
    --sky-top: #2f7fd4;
    --sky-mid: #79b9ee;
    --panel-light: #5f86c4;
    --panel-blue: #2c4f92;
    --panel-deep: #1b2f5e;
  }
  * { box-sizing: border-box; margin: 0; padding: 0; }
  html, body {
    width: 1200px; height: 844px; overflow: hidden;
    background: var(--bg);
    font-family: "Open Sans", Arial, sans-serif;
  }
  .sheet {
    position: relative; width: 1200px; height: 844px;
    display: flex; align-items: center; justify-content: center; gap: 60px;
  }
  .card {
    width: 520px; height: 297px; border-radius: 4px;
    position: relative; overflow: hidden;
    box-shadow: 0 10px 24px rgba(0,0,0,.18);
  }

  /* Front */
  .card-front { background: var(--card-black); color: var(--text-light); }
  .brand-lockup {
    position: absolute; left: 0; right: 0; top: 46px;
    display: flex; align-items: center; justify-content: center; gap: 12px;
  }
  .brand-mark {
    width: 30px; height: 30px; border-radius: 50%;
    background: var(--brand-gold); flex: none;
  }
  .brand-name {
    font-weight: 700; font-size: 32px; line-height: 40px;
    color: var(--brand-blue); white-space: nowrap;
  }
  .rule {
    position: absolute; left: 0; right: 0; height: 1px; background: var(--rule-blue);
  }
  .rule-top { top: 104px; }
  .rule-bottom { bottom: 34px; }
  .contact {
    position: absolute; left: 0; right: 0; top: 118px;
    text-align: center;
  }
  .person-name {
    font-weight: 700; font-size: 15px; line-height: 20px;
    color: var(--brand-gold); text-transform: uppercase; margin-bottom: 8px;
  }
  .contact-line {
    font-size: 13px; line-height: 21px;
    display: flex; align-items: center; justify-content: center; gap: 7px;
  }
  .contact-line svg { width: 11px; height: 11px; fill: var(--brand-gold); }
  .license {
    position: absolute; left: 0; right: 0; top: 218px;
    text-align: center; font-size: 13.5px; line-height: 20px;
  }
  .license-label { font-weight: 700; color: var(--brand-gold); }

  /* Back */
  .card-back { position: relative; }
  .back-photo {
    position: absolute; inset: 0;
    background: linear-gradient(172deg,
      var(--sky-top) 0%, var(--sky-mid) 46%,
      var(--panel-light) 50%, var(--panel-blue) 68%, var(--panel-deep) 100%);
  }
  .back-lockup {
    position: absolute; left: 0; right: 0; top: 92px;
    display: flex; align-items: center; justify-content: center; gap: 14px;
  }
  .back-lockup .brand-mark { width: 64px; height: 64px; }
  .back-lockup .brand-name { color: #ffffff; font-size: 26px; }
</style>
</head>
<body>
  <main class="sheet">
    <section class="card card-front">
      <div class="brand-lockup">
        <span class="brand-mark" aria-hidden="true"></span>
        <span class="brand-name">Velk Partners Building</span>
      </div>
      <div class="rule rule-top"></div>
      <div class="contact">
        <p class="person-name">Paul Osterby</p>
        <p class="contact-line">
          <svg viewBox="0 0 24 24" aria-hidden="true"><path d="M6.6 10.8a15 15 0 0 0 6.6 6.6l2.2-2.2a1 1 0 0 1 1-.25 11.4 11.4 0 0 0 3.6.57 1 1 0 0 1 1 1V20a1 1 0 0 1-1 1A17 17 0 0 1 3 4a1 1 0 0 1 1-1h3.5a1 1 0 0 1 1 1c0 1.25.2 2.45.57 3.57a1 1 0 0 1-.25 1z"/></svg>
          (619) 555-0187
        </p>
        <p class="contact-line">
          <svg viewBox="0 0 24 24" aria-hidden="true"><path d="M2 5h20v14H2V5zm2 2v.5l8 6 8-6V7H4z"/></svg>
          paul@velkpartners.example
        </p>
      </div>
      <p class="license"><span class="license-label">LICENSE:</span> CSLB# 3867140</p>
      <div class="rule rule-bottom"></div>
    </section>

    <section class="card card-back">
      <div class="back-photo" role="img" aria-label="Photograph of rooftop solar panels under a bright blue San Diego sky"></div>
      <div class="back-lockup">
        <span class="brand-mark" aria-hidden="true"></span>
        <span class="brand-name">Velk Partners Building</span>
      </div>
    </section>
  </main>
</body>
</html>
```